Card Design for my dog training business Brightpaw Obedience

Need a business card design for my dog training business with my new logo. Want the card to come off professional yet fun. Want it to be very eye catchy as well. I normally have these at vet clinics, pet stores, and groomers. so need it to look better than my competitors.
Target Market(s)
dog owners
Industry/Entity Type
Dog Training
Contact Information for Business Card
needs logo, my name and info
Font styles to use
Serif
Colors
0255a3
ffffff
ec1f27
000000
333333
fbfbfb
Requirements
Must have
- Brightpaw Obedience
- Felix Orland
- 415 903 2276
- info@brightpawobedience.example
- www.brightpawobedience.example

```html
<!DOCTYPE html>
<html lang="en">
<head>
<meta charset="utf-8">
<title>Brightpaw Obedience – Business Card</title>
<link rel="stylesheet" href="https://fonts.googleapis.com/css2?family=Noto+Serif:ital,wght@0,400;0,700;1,400&display=swap">
<style>
  :root {
    --backdrop: #2b2b2b;
    --card-black: #1e1e20;
    --panel-grey: #3a3c3f;
    --silver: #c9c9c9;
    --muted: #9a9a9a;
    --brand-blue: #0255a3;
    --name-blue: #1a8fd6;
    --brand-red: #ec1f27;
    --white: #fbfbfb;
  }
  * { margin: 0; padding: 0; box-sizing: border-box; }
  html, body {
    width: 799px; height: 1200px; overflow: hidden;
    background: var(--backdrop);
    font-family: "Noto Serif", Georgia, serif;
  }
  .sheet {
    position: relative; width: 799px; height: 1200px;
    display: flex; flex-direction: column; align-items: center;
    justify-content: center; gap: 110px;
  }
  .card {
    position: relative; width: 620px; height: 354px;
    background: var(--card-black);
    box-shadow: 0 14px 30px rgba(0,0,0,.45);
    overflow: hidden;
  }
  /* front */
  .front .brand-lockup {
    position: absolute; left: 0; right: 0; top: 104px;
    display: flex; flex-direction: column; align-items: center; gap: 14px;
  }
  .brand-mark {
    width: 22px; height: 22px; border-radius: 50%;
    background: var(--silver);
  }
  .brand-name {
    color: var(--silver); font-size: 30px; font-weight: 400;
    letter-spacing: .5px;
  }
  .tagline {
    font-style: italic; font-size: 14px; white-space: nowrap;
  }
  .front .tagline {
    position: absolute; left: 0; right: 0; top: 256px;
    text-align: center; color: var(--muted);
  }
  /* back */
  .back .swoosh { position: absolute; inset: 0; }
  .back .brand-lockup {
    position: absolute; left: 34px; top: 62px;
    display: flex; align-items: center; gap: 10px;
  }
  .back .brand-name { font-size: 23px; }
  .back .brand-mark { width: 16px; height: 16px; }
  .person {
    position: absolute; right: 40px; top: 96px; text-align: right;
  }
  .person-name { color: var(--name-blue); font-size: 22px; }
  .person-role { color: var(--muted); font-size: 13px; margin-top: 2px; }
  .contacts {
    position: absolute; right: 34px; top: 246px;
    list-style: none; text-align: right;
  }
  .contacts li {
    display: flex; justify-content: flex-end; align-items: center; gap: 12px;
    color: var(--white); font-size: 14px; line-height: 23px;
  }
  .contacts svg { width: 14px; height: 14px; fill: var(--white); }
  .back .tagline {
    position: absolute; right: 40px; top: 318px;
    color: var(--white);
  }
</style>
</head>
<body>
<main class="sheet">
  <section class="card front" aria-label="Card front">
    <div class="brand-lockup">
      <span class="brand-mark"></span>
      <span class="brand-name">Brightpaw Obedience</span>
    </div>
    <p class="tagline">“Kind, patient training for every dog we meet.”</p>
  </section>

  <section class="card back" aria-label="Card back">
    <svg class="swoosh" viewBox="0 0 620 354" preserveAspectRatio="none" aria-hidden="true">
      <path d="M0 214 C150 226 300 266 430 250 C520 238 580 212 620 200 L620 354 L0 354 Z" fill="var(--panel-grey)"/>
      <path d="M0 170 C90 176 180 212 300 232 C220 222 120 194 0 186 Z" fill="var(--brand-red)"/>
      <path d="M60 184 C170 200 270 246 400 240 C490 236 570 206 620 184 L620 192 C570 216 490 248 400 250 C270 256 170 210 60 184 Z" fill="var(--brand-blue)"/>
    </svg>

    <div class="brand-lockup">
      <span class="brand-mark"></span>
      <span class="brand-name">Brightpaw Obedience</span>
    </div>

    <div class="person">
      <p class="person-name">Felix Orland</p>
      <p class="person-role">Dog Trainer</p>
    </div>

    <ul class="contacts">
      <li>415 903 2276
        <svg viewBox="0 0 16 16" aria-label="Phone"><path d="M1 5c0-2 2-3 7-3s7 1 7 3v1h-4V5H5v1H1z"/><rect x="3" y="7" width="10" height="7" rx="1"/></svg>
      </li>
      <li>info@brightpawobedience.example
        <svg viewBox="0 0 16 16" aria-label="Email"><path d="M1 3h14v10H1z M2 4l6 5 6-5" fill="none" stroke="#fbfbfb" stroke-width="1.4"/></svg>
      </li>
      <li>www.brightpawobedience.example
        <svg viewBox="0 0 16 16" aria-label="Website"><circle cx="8" cy="8" r="6.5" fill="none" stroke="#fbfbfb" stroke-width="1.4"/><path d="M1.5 8h13 M8 1.5c-3 3-3 10 0 13 M8 1.5c3 3 3 10 0 13" fill="none" stroke="#fbfbfb" stroke-width="1.2"/></svg>
      </li>
    </ul>
    <p class="tagline">“Kind, patient training for every dog we meet.”</p>
  </section>
</main>
</body>
</html>
```